Design a business card
Business name: Harbourline Growth Advisory
Improving Business Profitibility

- An Overview of the Business & Service:

Business Performance Consulting

- The Target Market: Small to medium-sized business

- Design Specifics:
White card, blue ink, moon eclipse

No Logo

Target Market(s)

Small to medium-sized business

Font styles to use
Sans Serif

```html
<!DOCTYPE html>
<html lang="en">
<head>
<meta charset="UTF-8">
<title>Harbourline Growth Advisory – Business Card</title>
<link href="https://fonts.googleapis.com/css2?family=Exo+2:wght@600&family=Arimo:wght@400&family=Questrial&display=swap" rel="stylesheet">
<style>
  :root {
    --page-bg: #d8d5d0;
    --card-light: #f1f1f3;
    --card-mid: #e2e3e7;
    --brand-blue: #174a82;
    --ink-dark: #2a2a2c;
    --ink-contact: #333336;
    --icon-blue: #3a5f93;
    --band-light: #4d6c9f;
    --band-dark: #0a1f4c;
    --moon-light: #c9c9c9;
    --moon-dark: #8f8f92;
  }
  html, body {
    margin: 0;
    width: 1200px;
    height: 970px;
    overflow: hidden;
    background: var(--page-bg);
  }
  .business-card {
    position: absolute;
    left: 60px;
    top: 185px;
    width: 1080px;
    height: 600px;
    border-radius: 36px;
    overflow: hidden;
    background: linear-gradient(100deg, var(--card-mid) 0%, var(--card-light) 45%, var(--card-mid) 100%);
    box-shadow: 0 0 0 2px rgba(255,255,255,0.7) inset, 0 10px 30px rgba(0,0,0,0.15);
  }
  .moon-visual {
    position: absolute;
    left: 529px;
    top: -9px;
    width: 546px;
    height: 546px;
    border-radius: 50%;
    background: radial-gradient(circle at 60% 45%, var(--moon-light) 0%, #b2b2b4 45%, var(--moon-dark) 100%);
    opacity: 0.85;
  }
  .company-name {
    position: absolute;
    left: 78px;
    top: 38px;
    margin: 0;
    font-family: "Exo 2", sans-serif;
    font-weight: 600;
    font-size: 55px;
    line-height: 1;
    letter-spacing: -0.5px;
    color: var(--brand-blue);
    white-space: nowrap;
  }
  .person-name {
    position: absolute;
    left: 79px;
    top: 113px;
    margin: 0;
    font-family: "Arimo", sans-serif;
    font-size: 34px;
    line-height: 1;
    color: var(--ink-dark);
  }
  .contact-list {
    position: absolute;
    left: 78px;
    top: 288px;
    margin: 0;
    padding: 0;
    list-style: none;
    font-family: "Questrial", sans-serif;
    font-size: 25px;
    color: var(--ink-contact);
  }
  .contact-item {
    display: flex;
    align-items: center;
    height: 38px;
  }
  .contact-item svg {
    width: 24px;
    height: 24px;
    margin-right: 12px;
    fill: var(--icon-blue);
    flex: none;
  }
  .footer-band {
    position: absolute;
    left: 0;
    bottom: 0;
    width: 100%;
    height: 80px;
    background: linear-gradient(90deg, var(--band-light) 0%, #3c5b91 40%, var(--band-dark) 70%, #0d2455 100%);
  }
</style>
</head>
<body>
  <div class="business-card">
    <div class="moon-visual" role="img" aria-label="Photograph of the full moon in soft grey tones"></div>

    <h1 class="company-name">HARBOURLINE GROWTH ADVISORY</h1>
    <p class="person-name">Desmond R Akerly</p>

    <ul class="contact-list">
      <li class="contact-item">
        <svg viewBox="0 0 24 24" aria-hidden="true"><path d="M7 1h10a2 2 0 0 1 2 2v18a2 2 0 0 1-2 2H7a2 2 0 0 1-2-2V3a2 2 0 0 1 2-2zm0 3v13h10V4H7zm5 15a1.2 1.2 0 1 0 0 2.4 1.2 1.2 0 0 0 0-2.4z"/></svg>
        (415) 208-3196
      </li>
      <li class="contact-item">
        <svg viewBox="0 0 24 24" aria-hidden="true"><path d="M6.6 10.8a15.1 15.1 0 0 0 6.6 6.6l2.2-2.2a1 1 0 0 1 1-.25 11.4 11.4 0 0 0 3.6.57 1 1 0 0 1 1 1V20a1 1 0 0 1-1 1A17 17 0 0 1 3 4a1 1 0 0 1 1-1h3.5a1 1 0 0 1 1 1c0 1.25.2 2.450.57 3.57a1 1 0 0 1-.25 1z"/></svg>
        (415) 208-3196
      </li>
      <li class="contact-item">
        <svg viewBox="0 0 24 24" aria-hidden="true"><path d="M2 5h20v14H2V5zm2 2v.4l8 5.2 8-5.2V7H4zm0 2.8V17h16V9.8l-8 5.2-8-5.2z"/></svg>
        desmond@harbourline.com
      </li>
      <li class="contact-item">
        <svg viewBox="0 0 24 24" aria-hidden="true"><path d="M12 2a10 10 0 1 0 0 20 10 10 0 0 0 0-20zm6.9 6h-2.9a15.6 15.6 0 0 0-1.4-3.6A8 8 0 0 1 18.9 8zM12 4c.8 1.2 1.5 2.5 1.9 4h-3.8c.4-1.5 1.1-2.8 1.9-4zM4.3 14a8 8 0 0 1 0-4h3.4a16 16 0 0 0 0 4H4.3zm.8 2H8a15.6 15.6 0 0 0 1.4 3.6A8 8 0 0 1 5.1 16zM8 8H5.1a8 8 0 0 1 4.3-3.6C8.8 5.5 8.3 6.7 8 8zm4 12c-.8-1.2-1.5-2.5-1.9-4h3.8c-.4 1.5-1.1 2.8-1.9 4zm2.3-6H9.7a14.6 14.6 0 0 1 0-4h4.6a14.6 14.6 0 0 1 0 4zm.3 5.6c.6-1.1 1.1-2.3 1.4-3.6h2.9a8 8 0 0 1-4.3 3.6zm1.7-5.6a16 16 0 0 0 0-4h3.4a8 8 0 0 1 0 4h-3.4z"/></svg>
        www.harbourline.com
      </li>
      <li class="contact-item">
        <svg viewBox="0 0 24 24" aria-hidden="true"><path d="M12 2a7 7 0 0 0-7 7c0 5.2 7 13 7 13s7-7.8 7-13a7 7 0 0 0-7-7zm0 9.5A2.5 2.5 0 1 1 12 6.5a2.5 2.5 0 0 1 0 5z"/></svg>
        48 Quayside Rd. Bellhaven Oregon 97310
      </li>
    </ul>

    <div class="footer-band"></div>
  </div>
</body>
</html>
```